Mastering Modern Vineyard Management

size of the ad - 8”x 10.75" plus 0.25" bleed
I would like an ad for a magazine that will stand out and make people want to read the ad.
The ad should not be crowded and people reading the ad will be able to read the text.
I would like it to be a creative and modern-day design.
the list of topics should not be the focus of the ad.
the text is attached.
If you decide to use people in the ad then please no ladies.
please note that leave over 1 inch for the bottom of the footer

```html
<!DOCTYPE html>
<html lang="en">
<head>
<meta charset="UTF-8">
<title>Real Estate Course – Mastering Modern Vineyard Management</title>
<link href="https://fonts.googleapis.com/css2?family=EB+Garamond:wght@600;700&family=Fira+Sans:wght@300;400;500;600;700&display=swap" rel="stylesheet">
<style>
  :root{
    --title-blue:#1f74bd;
    --navy:#1a4a80;
    --band-navy:#0b4a84;
    --accent-blue:#2573b9;
    --yellow:#f4e52c;
    --panel-grey:#ebebeb;
    --ink:#1f1f1f;
    --tick-orange:#e8532a;
    --white:#ffffff;
  }
  *{margin:0;padding:0;box-sizing:border-box}
  html,body{width:935px;height:1200px;overflow:hidden;background:var(--white)}
  body{font-family:"Fira Sans",sans-serif;color:var(--ink)}
  .ad{position:relative;width:935px;height:1200px;overflow:hidden}

  .hero{position:absolute;left:0;top:0;width:935px;height:693px;
    background:linear-gradient(180deg,#b9d3ea 0%,#dfe9f2 28%,#e9eef2 45%,#5f86a6 62%,#2f5a7e 78%,#3f6a3c 92%,#2f5230 100%)}
  .headline{position:absolute;left:0;right:0;top:40px;text-align:center;font-family:"EB Garamond",serif}
  .headline .course{font-size:63px;font-weight:700;color:var(--title-blue);letter-spacing:.5px;line-height:1}
  .headline .subtitle{margin-top:18px;font-size:34px;font-weight:700;color:var(--navy);line-height:1.18;letter-spacing:.3px}

  .tagline-band{position:absolute;left:0;top:693px;width:935px;height:65px;background:var(--panel-grey);
    display:flex;align-items:center;justify-content:center}
  .tagline{font-size:29px;font-weight:600;color:var(--accent-blue)}

  .info-band{position:absolute;left:0;top:758px;width:935px;height:113px;background:var(--band-navy);color:var(--white)}
  .info-col{position:absolute;top:0;height:113px;display:flex;flex-direction:column;justify-content:center;align-items:center;text-align:center}
  .info-col .main{font-weight:300;font-size:31px;line-height:1.05}
  .info-col .hi{color:var(--yellow);font-weight:600}
  .col-location{left:30px;width:346px}
  .col-location .hi{font-size:16px;margin-top:6px}
  .col-days{left:376px;width:305px}
  .col-days .hi{font-size:27px;margin-top:2px}
  .col-start{left:681px;width:254px}
  .col-start .hi{font-size:29px;font-weight:700;margin-top:0}
  .divider{position:absolute;top:18px;width:2px;height:78px;background:#9fb3c9}

  .details{position:absolute;left:0;top:871px;width:935px;height:202px;background:var(--panel-grey)}
  .perks{position:absolute;left:56px;top:30px;list-style:none}
  .perks li{display:flex;align-items:flex-start;font-size:18.5px;font-weight:500;line-height:1.2;margin-bottom:12px}
  .perks svg{flex:none;width:20px;height:20px;margin-right:26px}
  .details .rule{position:absolute;left:456px;top:22px;width:2px;height:150px;background:#b5b5b5}
  .topics{position:absolute;left:488px;top:20px}
  .topics h2{font-size:21px;font-weight:700;color:var(--title-blue);letter-spacing:.2px}
  .topic-grid{display:grid;grid-template-columns:183px 150px;row-gap:5px;margin-top:6px;list-style:none}
  .topic-grid li{display:flex;align-items:center;font-size:14px;line-height:16px}
  .topic-grid svg{width:10px;height:10px;margin-right:6px;flex:none}

  .footer{position:absolute;left:0;top:1073px;width:935px;height:127px;background:var(--white)}
  .org{position:absolute;left:56px;top:28px;color:var(--title-blue);font-weight:700}
  .org .name{font-size:19px;line-height:1.1}
  .org .parent{font-size:11px;color:var(--navy);margin-top:6px;letter-spacing:.2px}
  .contact{position:absolute;left:286px;top:20px;font-size:12px;line-height:19px;color:var(--ink)}
  .contact .row{display:flex;align-items:center;gap:6px}
  .contact svg{width:11px;height:11px;flex:none}
  .contact .gap{margin-left:14px}
  .contact .sponsor{font-size:9.5px;margin-top:1px}
  .partner{position:absolute;left:652px;top:28px;width:232px;color:var(--navy);font-family:"EB Garamond",serif;font-weight:600;text-align:left}
  .partner .name{display:flex;align-items:center;gap:8px;font-size:21px;letter-spacing:.5px}
  .partner .mark{width:28px;height:28px;background:#2d5d80;flex:none}
  .partner .sub{font-size:10px;margin-top:6px}
</style>
</head>
<body>
<main class="ad">
  <section class="hero" role="img" aria-label="Photo of modern glass office towers rising above green trees under a cloudy sky">
    <header class="headline">
      <h1 class="course">REAL ESTATE COURSE</h1>
      <p class="subtitle">MASTERING MODERN VINEYARD<br>MANAGEMENT</p>
    </header>
  </section>

  <section class="tagline-band"><p class="tagline">Investing in knowledge is investing in opportunities</p></section>

  <section class="info-band">
    <div class="info-col col-location"><span class="main">Location: MONSEY</span><span class="hi">Remote: for out of MONEY Area</span></div>
    <div class="divider" style="left:375px"></div>
    <div class="info-col col-days"><span class="main">10 WEDNESDAY</span><span class="hi">7:30 PM –9:30 PM</span></div>
    <div class="divider" style="left:680px"></div>
    <div class="info-col col-start"><span class="main">STARTING</span><span class="hi">MARCH 8</span></div>
  </section>

  <section class="details">
    <ul class="perks">
      <li><svg viewBox="0 0 20 20"><rect x="1.5" y="3.5" width="15" height="15" fill="none" stroke="var(--tick-orange)" stroke-width="2"/><path d="M5 10l4 4 9-11" fill="none" stroke="var(--tick-orange)" stroke-width="2.6"/></svg>Limited Partial Scholarships</li>
      <li><svg viewBox="0 0 20 20"><rect x="1.5" y="3.5" width="15" height="15" fill="none" stroke="var(--tick-orange)" stroke-width="2"/><path d="M5 10l4 4 9-11" fill="none" stroke="var(--tick-orange)" stroke-width="2.6"/></svg>Early Bird Special</li>
      <li><svg viewBox="0 0 20 20"><rect x="1.5" y="3.5" width="15" height="15" fill="none" stroke="var(--tick-orange)" stroke-width="2"/><path d="M5 10l4 4 9-11" fill="none" stroke="var(--tick-orange)" stroke-width="2.6"/></svg><span>For those that started or<br>would like to go into real estate</span></li>
    </ul>
    <div class="rule"></div>
    <div class="topics">
      <h2>TOPICS: PARTIAL LISTING</h2>
      <ul class="topic-grid">
        <li><svg viewBox="0 0 10 10"><circle cx="5" cy="5" r="5" fill="var(--accent-blue)"/><path d="M2.6 5.2l1.6 1.6 3.2-3.4" fill="none" stroke="#fff" stroke-width="1.3"/></svg>Investment strategies</li>
        <li><svg viewBox="0 0 10 10"><circle cx="5" cy="5" r="5" fill="var(--accent-blue)"/><path d="M2.6 5.2l1.6 1.6 3.2-3.4" fill="none" stroke="#fff" stroke-width="1.3"/></svg>Due diligence</li>
        <li><svg viewBox="0 0 10 10"><circle cx="5" cy="5" r="5" fill="var(--accent-blue)"/><path d="M2.6 5.2l1.6 1.6 3.2-3.4" fill="none" stroke="#fff" stroke-width="1.3"/></svg>Property management</li>
        <li><svg viewBox="0 0 10 10"><circle cx="5" cy="5" r="5" fill="var(--accent-blue)"/><path d="M2.6 5.2l1.6 1.6 3.2-3.4" fill="none" stroke="#fff" stroke-width="1.3"/></svg>Financing</li>
        <li><svg viewBox="0 0 10 10"><circle cx="5" cy="5" r="5" fill="var(--accent-blue)"/><path d="M2.6 5.2l1.6 1.6 3.2-3.4" fill="none" stroke="#fff" stroke-width="1.3"/></svg>Real estate Legal basics</li>
        <li><svg viewBox="0 0 10 10"><circle cx="5" cy="5" r="5" fill="var(--accent-blue)"/><path d="M2.6 5.2l1.6 1.6 3.2-3.4" fill="none" stroke="#fff" stroke-width="1.3"/></svg>Underwriting</li>
        <li><svg viewBox="0 0 10 10"><circle cx="5" cy="5" r="5" fill="var(--accent-blue)"/><path d="M2.6 5.2l1.6 1.6 3.2-3.4" fill="none" stroke="#fff" stroke-width="1.3"/></svg>Dealing with brokers</li>
        <li><svg viewBox="0 0 10 10"><circle cx="5" cy="5" r="5" fill="var(--accent-blue)"/><path d="M2.6 5.2l1.6 1.6 3.2-3.4" fill="none" stroke="#fff" stroke-width="1.3"/></svg>Sourcing deals</li>
        <li><svg viewBox="0 0 10 10"><circle cx="5" cy="5" r="5" fill="var(--accent-blue)"/><path d="M2.6 5.2l1.6 1.6 3.2-3.4" fill="none" stroke="#fff" stroke-width="1.3"/></svg>Tax fundamentals</li>
        <li><svg viewBox="0 0 10 10"><circle cx="5" cy="5" r="5" fill="var(--accent-blue)"/><path d="M2.6 5.2l1.6 1.6 3.2-3.4" fill="none" stroke="#fff" stroke-width="1.3"/></svg>Syndication</li>
      </ul>
    </div>
  </section>

  <footer class="footer">
    <div class="org">
      <p class="name">HARVEST PATH<br>CAREER NETWORK</p>
      <p class="parent">A NON-PROFIT OF MEADOWLINE TRUST</p>
    </div>
    <div class="contact">
      <div class="row"><svg viewBox="0 0 12 12"><circle cx="6" cy="6" r="5.3" fill="none" stroke="var(--accent-blue)"/><path d="M6 9.2S3.8 6.8 3.8 5.2a2.2 2.2 0 0 1 4.4 0C8.2 6.8 6 9.2 6 9.2z" fill="var(--accent-blue)"/></svg>Monsey- out of Monsey Area</div>
      <div class="row"><svg viewBox="0 0 12 12"><circle cx="6" cy="6" r="5.3" fill="none" stroke="var(--accent-blue)"/><path d="M4 3.2l1.2 1.4-.6.8a4 4 0 0 0 1.9 1.9l.8-.6L8.7 8l-.7.9C5.6 8.7 3.3 6.4 3.1 4z" fill="var(--accent-blue)"/></svg>555 201 4400 x 120</div>
      <div class="row"><svg viewBox="0 0 12 12"><circle cx="6" cy="6" r="5.3" fill="none" stroke="var(--accent-blue)"/><rect x="3.3" y="4.2" width="5.4" height="3.8" fill="var(--accent-blue)"/></svg>info@harvestpath.org
        <svg class="gap" viewBox="0 0 12 12"><circle cx="6" cy="6" r="5.3" fill="none" stroke="var(--accent-blue)"/><circle cx="6" cy="6" r="3" fill="none" stroke="var(--accent-blue)"/><path d="M3 6h6M6 3v6" stroke="var(--accent-blue)" stroke-width=".8"/></svg>www.harvestpath.org</div>
      <p class="sponsor">Sponsored in part by the Harold Brennan family foundation</p>
    </div>
    <div class="partner">
      <div class="name"><span class="mark"></span>CRESTFIELD TITLE GROUP</div>
      <p class="sub">A Crestfield Land Services Company</p>
    </div>
  </footer>
</main>
</body>
</html>
```